Polished Comb salon has created a lotion and needs help titling.Tides by polished comb ?Polis

The product is for a lotion bottle , my prototype lotion bottle size is an 8oz black lotion bottle with pump. I want the label in florescent green. It should tap into the emotion of potential buyers. The design should say choose me 😀(not literally ). Though the text should be clear and punchy . I.e " the skin multi-vitamin." I'm looking for a designer intrigued by the thought of my lotion. The label should be georgeous,informative, with visuals that immediately convey what my product is and how it works.Not distracting, but clear and punchy, with no expectation of someone to read more than a couple of words.The text should support the visual in a way the visual could not. It seems that nowadays visuals are taking over with very little text. The font,color , or punch of color should be enticing.
So here are some particular ideas of points about the lotion that could possibly be put on back as is done by lotion makers.
.ingredients
.TSA approved
.portion of proceeds go to lunch for little ones
.TC circled ( which is for pending trademark)
. I would like the word New in fluorescent on the bottle
.P.O Box address of place of manufacturing product.
. To help skin stay slightly moist,soft,and flexible with a smooth fine grained texture.

Target Market(s)

its a lotion so I want it available for all

Industry/Entity Type

Barber

Colors
9bcb3c

Requirements
Must have
• the word" Tides" and By polished comb...the word new on the bottle visible

```html
<!DOCTYPE html>
<html lang="en">
<head>
<meta charset="utf-8">
<title>Tides by Polished Comb – Lotion Label</title>
<link rel="stylesheet" href="https://fonts.googleapis.com/css2?family=Montserrat:wght@400;500;600;700&display=swap">
<style>
  :root {
    --backdrop-light: #f2f2f2;
    --backdrop-dark: #c9c9c9;
    --label-black: #1b1b1b;
    --fluoro-green: #a6d646;
    --green-text: #b5e04f;
    --ink: #1f1f1f;
    --badge-green: #bfe34a;
    --white: #ffffff;
  }
  * { box-sizing: border-box; margin: 0; padding: 0; }
  html, body { width: 1200px; height: 1200px; overflow: hidden; }
  body {
    background: radial-gradient(ellipse at 50% 40%, var(--backdrop-light) 0%, #dedede 60%, var(--backdrop-dark) 100%);
    font-family: "Montserrat", sans-serif;
    position: relative;
  }
  .label {
    position: absolute;
    left: 240px; top: 195px;
    width: 720px; height: 810px;
    background: var(--label-black);
    border-radius: 14px;
    overflow: hidden;
    box-shadow: 0 20px 50px rgba(0,0,0,0.25);
  }
  .label__top {
    position: absolute;
    left: 0; top: 0;
    width: 720px; height: 486px;
    background: var(--fluoro-green);
    border-radius: 0 0 90px 90px;
  }
  .badge-new {
    position: absolute;
    left: 66px; top: 46px;
    width: 116px; height: 116px;
    border-radius: 50%;
    background: var(--badge-green);
    box-shadow: 0 0 0 6px rgba(255,255,255,0.25);
    display: flex; align-items: center; justify-content: center;
    transform: rotate(-18deg);
    color: var(--white);
    font-weight: 700;
    font-size: 30px;
    letter-spacing: 1px;
  }
  .brand {
    position: absolute;
    left: 100px; top: 150px;
    display: flex; align-items: center; gap: 22px;
  }
  .brand__name {
    font-weight: 500;
    font-size: 190px;
    line-height: 1;
    letter-spacing: -6px;
    color: var(--ink);
  }
  .brand__dot {
    width: 70px; height: 70px;
    border-radius: 50%;
    background: var(--ink);
    margin-top: 20px;
  }
  .brand__byline {
    position: absolute;
    left: 110px; top: 352px;
    font-weight: 700;
    font-size: 25px;
    letter-spacing: 0.5px;
    color: var(--ink);
  }
  .tagline-pill {
    position: absolute;
    left: 108px; top: 404px;
    width: 464px; height: 58px;
    background: var(--ink);
    border-radius: 12px;
    display: flex; align-items: center; justify-content: center;
    color: var(--green-text);
    font-weight: 700;
    font-size: 31px;
    letter-spacing: 0.3px;
  }
  .benefit {
    position: absolute;
    left: 0; top: 540px;
    width: 720px;
    text-align: center;
    color: var(--green-text);
    font-weight: 700;
    font-size: 33px;
    line-height: 46px;
  }
  .body-copy {
    position: absolute;
    left: 120px; top: 640px;
    width: 480px;
    color: var(--green-text);
    font-weight: 500;
    font-size: 19px;
    line-height: 27px;
    text-align: justify;
    text-align-last: center;
  }
  .net-weight {
    position: absolute;
    left: 0; top: 742px;
    width: 720px;
    text-align: center;
    color: var(--green-text);
    font-weight: 600;
    font-size: 29px;
  }
</style>
</head>
<body>
  <section class="label" aria-label="Tides lotion bottle label">
    <div class="label__top">
      <div class="badge-new">NEW</div>
      <div class="brand">
        <span class="brand__name">Tides</span>
        <span class="brand__dot" aria-hidden="true"></span>
      </div>
      <div class="brand__byline">BY POLISHED COMB</div>
      <div class="tagline-pill">THE SKIN MULTI-VITAMIN</div>
    </div>
    <p class="benefit">KEEPS SKIN SOFT,<br>SMOOTH AND SLIGHTLY MOIST</p>
    <p class="body-copy">Lorem ipsum dolor sit amet, consectetur adipisicing elit, sed do eiusmod tempor incididunt ut labore et dolore magna aliqua.</p>
    <p class="net-weight">Net Weight: 8oz</p>
  </section>
</body>
</html>
```